Buchcover-Design für romanhafte Biografie aus der Nachkriegszeit
Zielgruppe
Meine Zielgruppe sind Leser von Biografien aus der Zeit des Nationalsozialismus bzw. der Nachkriegszeit. Es handelt sich um eine 'romanhafte' Biografie. Ich möchte das Erzählerische betonen. Eigentlich ist es eine Liebesgeschichte.
Aufgabenstellung
Autor: Tobias Wenzel
Deutscher Titel: Wege im Nebel
Untertitel: Ein stilles Zeugnis aus den bewegten Jahren
Englischer Titel: Paths in Fog
Untertitel: A quiet account from turbulent years
Ich benötige zwei Versionen von demselben Cover: einmal den deutschen Titel, einmal den englischen Titel (keine Hardcoverausgabe)
In meiner romanhaften Biografie aus der Nazi- und Nachkriegszeit beschreibe ich das Leben einer Frau (meiner Mutter), die sich als junges Mädchen in einen jugendlichen Funktionär der Hitlerjungend verliebt. Er ist mutig, sportlich und unbeschwert - eine Art Siegfried. Die Liebe endet tragisch, da er 1942 in Stalingrad fällt. Da ist die junge Frau achtzehn Jahre alt. (Die Fotos sind aus dieser Zeit.) Ort der Handlung ist Duisburg.
Die junge Frau kann ihre Liebe niemals vergessen, geht aber nach dem Krieg eine neue Beziehung ein. Dieser Mann ist vier Jahre jünger als sie, Mediziner und unbelastet von Kriegserinnerungen. Er ist das Gegenteil ihrer ersten Liebe: Brillenträger, sehr intelligent und ein wenig gefühlskalt.
Die junge Frau steht also zwischen zwei Männern - einem Toten, der für sie nie gestorben ist, und einem Lebenden. Sie steht mit einem Fuß in der alten Zeit (des Nationalsozialismus) und mit dem anderen Fuß in der neuen Zeit.
Text für Veltora:
“Es die falsche Zeit, sich zu verlieben”, sagte der Vater. “Und es ist der falsche Mann.”
Aber Helga hört nicht auf ihn, denn Konrad ist ihre Sandkastenliebe, der Sohn des besten Freundes ihres Vaters. Früh tritt Konrad der Hitlerjugend bei, ihre Freundin Tilde geht zum Bund Deutscher Mädel. Helga ist immer dabei, denn sie liebt Konrad und alles, was er ist.
Dann beginnt der Krieg. Hat der Vater doch recht gehabt?

```html
<!DOCTYPE html>
<html lang="de">
<head>
<meta charset="utf-8">
<title>Wege im Nebel – Umschlag</title>
<link rel="stylesheet" href="https://fonts.googleapis.com/css2?family=UnifrakturMaguntia&family=EB+Garamond:wght@500&family=Open+Sans:wght@300;400&display=swap">
<style>
  :root {
    --paper-light: #d6bb9c;
    --paper-mid: #b8967a;
    --paper-dark: #7d5a47;
    --doc-red: #8c5b47;
    --doc-form: #b39580;
    --doc-lower: #c8a785;
    --rose: #a5766d;
    --leaf: #4f5a3e;
    --stamp: #6e4f6a;
    --rule: rgba(70, 40, 25, 0.35);
    --photo-light: #cdbca8;
    --photo-dark: #4a3a30;
    --ink-white: #f7f4ef;
    --shadow: rgba(40, 22, 12, 0.8);
  }
  * { margin: 0; padding: 0; box-sizing: border-box; }
  html, body { width: 1200px; height: 910px; overflow: hidden; background: #ffffff; }
  .cover { position: relative; width: 1200px; height: 910px; overflow: hidden; color: var(--ink-white); }
  .collage { position: absolute; inset: 0; width: 1200px; height: 910px; }
  .portrait-main {
    position: absolute; left: 712px; top: 232px; width: 456px; height: 612px;
    transform: rotate(1deg);
    background: radial-gradient(ellipse at 50% 42%, var(--photo-light) 0%, #a08c79 40%, #6a5646 75%, var(--photo-dark) 100%);
    box-shadow: 0 2px 10px rgba(0,0,0,0.3);
  }
  .portrait-hardware { position: absolute; left: 712px; top: 232px; width: 456px; height: 612px; transform: rotate(1deg); }
  .portrait-small {
    position: absolute; left: 119px; top: 697px; width: 185px; height: 230px;
    transform: rotate(-3deg);
    background: radial-gradient(ellipse at 50% 40%, #c7b39b 0%, #8e7865 60%, #5b4637 100%);
  }
  .barcode-field { position: absolute; left: 315px; top: 727px; width: 223px; height: 141px; background: #ffffff; }
  .title-front {
    position: absolute; left: 640px; top: 22px; width: 545px; text-align: center;
    font-family: "UnifrakturMaguntia", serif; font-weight: 400; font-size: 92px; line-height: 1;
    text-shadow: 0 2px 6px var(--shadow);
  }
  .title-front .small { font-size: 52px; }
  .subtitle-front {
    position: absolute; left: 698px; top: 146px; width: 400px; text-align: center;
    font-family: "UnifrakturMaguntia", serif; font-size: 30px; line-height: 38px;
    word-spacing: 6px; text-shadow: 0 2px 4px var(--shadow);
  }
  .author-front {
    position: absolute; left: 700px; top: 842px; width: 420px; text-align: center;
    font-family: "Open Sans", sans-serif; font-weight: 400; font-size: 40px; letter-spacing: 4px;
  }
  .spine-title, .spine-author { position: absolute; white-space: nowrap; transform-origin: left top; transform: rotate(90deg); }
  .spine-title {
    left: 622px; top: 33px;
    font-family: "UnifrakturMaguntia", serif; font-size: 54px; line-height: 46px;
    text-shadow: 0 2px 5px var(--shadow);
  }
  .spine-author {
    left: 622px; top: 622px;
    font-family: "Open Sans", sans-serif; font-weight: 300; font-size: 33px; line-height: 44px; letter-spacing: 1px;
  }
  .blurb {
    position: absolute; left: 61px; top: 250px; width: 460px;
    font-family: "EB Garamond", serif; font-weight: 500; font-size: 22.5px; line-height: 27.6px;
    text-shadow: 0 1px 3px var(--shadow), 0 0 7px var(--shadow);
  }
  .blurb .quote { text-align: center; margin-bottom: 26px; padding: 0 24px; }
  .blurb .body { text-align: justify; margin-bottom: 28px; }
  .blurb .closing { text-align: center; }
</style>
</head>
<body>
<div class="cover">
  <svg class="collage" viewBox="0 0 1200 910" role="img" aria-label="Collage aus alten Ausweisdokumenten, Formularen, Stempeln und verblichenen Rosen in Sepiatönen">
    <defs>
      <linearGradient id="base" x1="0" y1="0" x2="1" y2="1">
        <stop offset="0" stop-color="#86604c"/>
        <stop offset="0.5" stop-color="#b39075"/>
        <stop offset="1" stop-color="#c9a989"/>
      </linearGradient>
      <radialGradient id="rose"><stop offset="0" stop-color="#9b6a63"/><stop offset="0.6" stop-color="#a5766d" stop-opacity="0.6"/><stop offset="1" stop-color="#a5766d" stop-opacity="0"/></radialGradient>
      <radialGradient id="leaf"><stop offset="0" stop-color="#4f5a3e" stop-opacity="0.85"/><stop offset="1" stop-color="#4f5a3e" stop-opacity="0"/></radialGradient>
      <radialGradient id="haze"><stop offset="0" stop-color="#e3cdb4" stop-opacity="0.7"/><stop offset="1" stop-color="#e3cdb4" stop-opacity="0"/></radialGradient>
    </defs>
    <rect width="1200" height="910" fill="url(#base)"/>
    <!-- upper right paper -->
    <rect x="700" y="0" width="500" height="240" fill="#c2a48c"/>
    <ellipse cx="930" cy="120" rx="260" ry="130" fill="url(#haze)"/>
    <!-- large red pass document -->
    <g transform="rotate(-7 260 280)">
      <rect x="-20" y="-20" width="560" height="580" fill="var(--doc-red)"/>
      <rect x="10" y="10" width="500" height="520" fill="none" stroke="var(--rule)" stroke-width="3"/>
      <rect x="22" y="22" width="476" height="496" fill="none" stroke="var(--rule)" stroke-width="1.5"/>
      <line x1="22" y1="170" x2="498" y2="170" stroke="var(--rule)" stroke-width="1.5"/>
      <line x1="22" y1="330" x2="498" y2="330" stroke="var(--rule)" stroke-width="1.5"/>
      <circle cx="175" cy="285" r="58" fill="none" stroke="rgba(60,30,20,0.35)" stroke-width="3"/>
      <circle cx="150" cy="90" r="13" fill="#6d4636" stroke="#a98a78" stroke-width="3"/>
      <circle cx="310" cy="225" r="13" fill="#6d4636" stroke="#a98a78" stroke-width="3"/>
    </g>
    <!-- form sheet with printed rules -->
    <g transform="rotate(0.5 550 300)">
      <rect x="392" y="80" width="318" height="470" fill="var(--doc-form)" opacity="0.95"/>
      <g stroke="var(--rule)" stroke-width="1">
        <line x1="400" y1="126" x2="705" y2="126"/><line x1="400" y1="143" x2="705" y2="143"/>
        <line x1="400" y1="160" x2="705" y2="160"/><line x1="400" y1="177" x2="705" y2="177"/>
        <line x1="400" y1="194" x2="705" y2="194"/><line x1="400" y1="211" x2="705" y2="211"/>
        <line x1="400" y1="228" x2="705" y2="228"/><line x1="400" y1="245" x2="705" y2="245"/>
        <line x1="400" y1="278" x2="705" y2="278"/><line x1="400" y1="295" x2="705" y2="295"/>
        <line x1="400" y1="312" x2="705" y2="312"/><line x1="400" y1="329" x2="705" y2="329"/>
        <line x1="400" y1="346" x2="705" y2="346"/><line x1="400" y1="363" x2="705" y2="363"/>
        <line x1="400" y1="380" x2="705" y2="380"/><line x1="400" y1="397" x2="705" y2="397"/>
        <line x1="400" y1="430" x2="705" y2="430"/><line x1="400" y1="525" x2="705" y2="525"/>
      </g>
    </g>
    <!-- lower documents -->
    <rect x="0" y="590" width="720" height="320" fill="var(--doc-lower)"/>
    <g transform="rotate(-2 560 760)">
      <rect x="440" y="595" width="270" height="330" fill="#c6a17e"/>
      <g stroke="var(--rule)" stroke-width="1">
        <line x1="450" y1="650" x2="705" y2="650"/><line x1="450" y1="690" x2="705" y2="690"/>
        <line x1="450" y1="720" x2="705" y2="720"/><line x1="450" y1="750" x2="705" y2="750"/>
        <line x1="450" y1="780" x2="705" y2="780"/><line x1="450" y1="810" x2="705" y2="810"/>
        <line x1="450" y1="840" x2="705" y2="840"/><line x1="450" y1="870" x2="705" y2="870"/>
        <line x1="570" y1="650" x2="570" y2="920"/><line x1="640" y1="650" x2="640" y2="920"/>
      </g>
    </g>
    <g transform="rotate(-3 150 760)">
      <rect x="15" y="610" width="420" height="320" fill="none" stroke="var(--rule)" stroke-width="2"/>
      <circle cx="70" cy="740" r="55" fill="none" stroke="rgba(90,60,60,0.35)" stroke-width="3"/>
      <circle cx="280" cy="860" r="50" fill="none" stroke="rgba(90,60,60,0.3)" stroke-width="3"/>
    </g>
    <line x1="0" y1="590" x2="720" y2="575" stroke="rgba(70,40,25,0.25)" stroke-width="2"/>
    <!-- roses and leaves -->
    <ellipse cx="570" cy="50" rx="110" ry="70" fill="url(#rose)"/>
    <ellipse cx="760" cy="30" rx="70" ry="50" fill="url(#rose)"/>
    <ellipse cx="1160" cy="110" rx="80" ry="90" fill="url(#rose)"/>
    <ellipse cx="1170" cy="770" rx="60" ry="90" fill="url(#rose)"/>
    <ellipse cx="1160" cy="190" rx="40" ry="18" fill="url(#leaf)"/>
    <ellipse cx="745" cy="130" rx="35" ry="28" fill="url(#leaf)"/>
    <ellipse cx="1000" cy="835" rx="40" ry="28" fill="url(#leaf)"/>
    <ellipse cx="425" cy="60" rx="30" ry="40" fill="url(#leaf)"/>
  </svg>

  <section class="back-cover">
    <div class="blurb">
      <p class="quote">“Es die falsche Zeit, sich zu verlieben”, sagte der Vater. “Und es ist der falsche Mann.”</p>
      <p class="body">Aber Helga hört nicht auf ihn, denn Konrad ist ihre Sandkastenliebe, der Sohn des besten Freundes ihres Vaters. Früh tritt Konrad der Hitlerjugend bei, ihre Freundin Tilde geht zum Bund Deutscher Mädel. Helga ist immer dabei, denn sie liebt Konrad und alles, was er ist.</p>
      <p class="closing">Dann beginnt der Krieg.<br>Hat der Vater doch recht gehabt?</p>
    </div>
    <div class="portrait-small" role="img" aria-label="Altes Passfoto einer jungen Frau auf einem Dokument"></div>
    <div class="barcode-field"></div>
  </section>

  <section class="spine">
    <div class="spine-title">Wege im Nebel</div>
    <div class="spine-author">TOBIAS WENZEL</div>
  </section>

  <section class="front-cover">
    <div class="portrait-main" role="img" aria-label="Gealtertes Schwarzweiß-Porträtfoto einer jungen Frau, auf ein Dokument geheftet"></div>
    <svg class="portrait-hardware" viewBox="0 0 456 612" aria-hidden="true">
      <line x1="120" y1="35" x2="270" y2="35" stroke="#8a7a6c" stroke-width="5" stroke-linecap="round"/>
      <line x1="240" y1="520" x2="420" y2="522" stroke="#6d5f54" stroke-width="3" stroke-linecap="round"/>
      <circle cx="395" cy="60" r="27" fill="#b9a898" stroke="#6f6257" stroke-width="7"/>
      <circle cx="48" cy="510" r="26" fill="#8f7f70" stroke="#5e5147" stroke-width="7"/>
      <circle cx="410" cy="330" r="70" fill="none" stroke="var(--stamp)" stroke-width="3" opacity="0.35"/>
    </svg>
    <h1 class="title-front">Wege <span class="small">im</span> Nebel</h1>
    <p class="subtitle-front">Ein stilles Zeugnis<br>aus den bewegten Jahren</p>
    <p class="author-front">TOBIAS WENZEL</p>
  </section>
</div>
</body>
</html>
```